IT Company that provides secure IT solutions and services to our customers

We need business cards and a logo for a new IT Solutions company just created based in Kuala Lumpur, Malaysia. But will also be serving other countries in the region. We provide secure data, voice solutions on mobile platforms. Our first offering is encrypted voice and data solutions for IOS, Android, Windows and BlackBerry devices.

Target Market(s)

large organizations Govt, Police, Defence, Anti-corruption, Legal, highly regulated industries such as Health-care, Financial, Banking, Insurance,

Industry/Entity Type

Information Technology

Contact Information for Business Card

VelmoraNet (Logo - colour is ORVEX blue)Roshan Adeel Managing Director Kryption IT Sdn. Bhd.5th Floor, Block D, Wisma PLB,No.14 Jalan Seri Melor,50470, Kuala LumpurMalaysia

Font styles to use
Sans Serif

Colors
3176b5
ec1f27
fbed22

Requirements
Must have
• VelmoraNet all in Blue like ORVEX blue. A logo design perhaps a play of VN, K with a dangling T (colour can be any)
Nice to have
• I want a clean crisp card, not too busy, easy to read.

```html
<!DOCTYPE html>
<html lang="en">
<head>
<meta charset="utf-8">
<title>VelmoraNet Business Card</title>
<link href="https://fonts.googleapis.com/css2?family=Open+Sans:wght@400;700&display=swap" rel="stylesheet">
<style>
  :root {
    --brand-blue: #1a5dae;
    --card-white: #ffffff;
    --panel-grey: #f3f4f6;
    --backdrop: #e9e7e4;
    --text-light: #ffffff;
  }
  * { margin: 0; padding: 0; box-sizing: border-box; }
  html, body {
    width: 1200px; height: 844px; overflow: hidden;
    background: var(--backdrop);
    font-family: "Open Sans", sans-serif;
  }
  .stage {
    position: relative; width: 1200px; height: 844px;
  }
  .card {
    position: absolute; top: 272px;
    width: 520px; height: 300px;
    background: var(--card-white);
    box-shadow: 0 6px 18px rgba(0,0,0,0.18);
    overflow: hidden;
  }
  .card-info { left: 50px; display: flex; }
  .card-brand { left: 630px; display: flex; align-items: center; justify-content: center; }

  .info-mark {
    width: 200px; height: 100%;
    background: var(--panel-grey);
    display: flex; flex-direction: column; align-items: center; justify-content: center; gap: 14px;
  }
  .mark-square {
    width: 92px; height: 92px;
    border: 5px solid var(--brand-blue);
  }
  .mark-name {
    color: var(--brand-blue); font-weight: 700; font-size: 20px; letter-spacing: 0.2px;
  }
  .info-panel {
    flex: 1; background: var(--brand-blue); color: var(--text-light);
    padding: 78px 34px 0 34px;
  }
  .person-name { font-weight: 700; font-size: 15px; line-height: 1.2; }
  .person-title { font-size: 12px; line-height: 1.3; margin-bottom: 26px; }
  .company-name { font-weight: 700; font-size: 15px; line-height: 1.25; }
  .company-address { font-size: 12.5px; line-height: 1.4; max-width: 270px; }

  .brand-lockup { display: flex; align-items: center; gap: 14px; }
  .brand-square { width: 46px; height: 46px; border: 3px solid var(--brand-blue); }
  .brand-name { color: var(--brand-blue); font-weight: 700; font-size: 38px; letter-spacing: 0.3px; }
</style>
</head>
<body>
<main class="stage">
  <section class="card card-info">
    <div class="info-mark">
      <div class="mark-square"></div>
      <div class="mark-name">VelmoraNet</div>
    </div>
    <div class="info-panel">
      <p class="person-name">Roshan Adeel</p>
      <p class="person-title">Managing Director</p>
      <p class="company-name">Velmora Net</p>
      <p class="company-address">Sdn. Bhd.5th Floor, Block D, Wisma PLB,No.14 Jalan Seri Melor, 50470, Kuala Lumpur Malaysia</p>
    </div>
  </section>

  <section class="card card-brand">
    <div class="brand-lockup">
      <div class="brand-square"></div>
      <span class="brand-name">VelmoraNet</span>
    </div>
  </section>
</main>
</body>
</html>
```